Business Card Design for Training Business

Clear Path Coaching is a new business that delivers training and other services with a focus on topics related to mental health and wellbeing, for example, Wellmind Response Course, Resilience etc. We have a strong focus on evidence-based psychology and neuroscience. I have a logo which I will upload with the brief, so please consider colours that work well with the logo.
Target Market(s)
Adults, workplaces (particularly government and not-for-profits)
Industry/Entity Type
Business
Contact Information for Business Card
Head Strong TrainingSamantha SellwoodDirector0438 770 850sam@headstrongtraining.com.auwww.headstrongtraining.com.au

```html
<!DOCTYPE html>
<html lang="en">
<head>
<meta charset="utf-8">
<title>Clear Path Coaching – Business Card</title>
<link rel="stylesheet" href="https://fonts.googleapis.com/css2?family=Open+Sans:wght@300;400;600;700&display=swap">
<style>
  :root {
    --backdrop: #e9e7e4;
    --card-white: #f8f8f7;
    --panel-brown: #6a5c56;
    --accent-teal: #2cc3c6;
    --wordmark-grey: #a9a9a9;
    --text-light: #ffffff;
  }
  html, body {
    margin: 0;
    padding: 0;
    width: 1200px;
    height: 1022px;
    overflow: hidden;
    background: var(--backdrop);
    font-family: "Open Sans", Arial, sans-serif;
  }
  .stage {
    width: 1200px;
    height: 1022px;
    display: flex;
    align-items: center;
    justify-content: center;
  }
  .business-card {
    position: relative;
    width: 960px;
    height: 560px;
    border-radius: 26px;
    overflow: hidden;
    background: var(--card-white);
    box-shadow: 0 14px 40px rgba(0,0,0,0.18);
  }
  .contact-panel {
    position: absolute;
    inset: 0;
  }
  .brand {
    position: absolute;
    left: 30px;
    top: 110px;
    width: 380px;
    display: flex;
    flex-direction: column;
    align-items: center;
  }
  .brand-mark {
    width: 150px;
    height: 150px;
  }
  .brand-name {
    margin-top: 30px;
    font-weight: 300;
    font-size: 25px;
    letter-spacing: 3px;
    text-transform: uppercase;
    color: var(--wordmark-grey);
    white-space: nowrap;
  }
  .contact-details {
    position: absolute;
    right: 62px;
    top: 108px;
    text-align: right;
    color: var(--text-light);
  }
  .person-name {
    margin: 0;
    font-weight: 700;
    font-size: 46px;
    line-height: 1.1;
  }
  .person-role {
    display: flex;
    justify-content: flex-end;
    align-items: center;
    gap: 14px;
    margin-top: 6px;
    font-size: 25px;
    color: var(--accent-teal);
  }
  .contact-icons {
    display: flex;
    gap: 10px;
  }
  .contact-icons svg {
    width: 22px;
    height: 22px;
  }
  .contact-lines {
    margin-top: 30px;
    font-size: 23px;
    line-height: 1.45;
    font-weight: 400;
  }
</style>
</head>
<body>
<main class="stage">
  <section class="business-card" aria-label="Clear Path Coaching business card">
    <svg class="contact-panel" viewBox="0 0 960 560" aria-hidden="true">
      <circle cx="1050" cy="170" r="620" fill="var(--panel-brown)" stroke="var(--accent-teal)" stroke-width="7"/>
    </svg>

    <div class="brand">
      <svg class="brand-mark" viewBox="0 0 150 150" aria-hidden="true">
        <circle cx="75" cy="75" r="70" fill="none" stroke="var(--accent-teal)" stroke-width="3"/>
      </svg>
      <div class="brand-name">Clear Path Coaching</div>
    </div>

    <div class="contact-details">
      <h1 class="person-name">Rebecca Tanfield</h1>
      <div class="person-role">
        <span>Director</span>
        <span class="contact-icons">
          <svg viewBox="0 0 24 24" aria-label="phone"><path d="M6.6 10.8a15 15 0 0 0 6.6 6.6l2.2-2.2a1 1 0 0 1 1-.25 11.4 11.4 0 0 0 3.6.6 1 1 0 0 1 1 1V20a1 1 0 0 1-1 1A17 17 0 0 1 3 4a1 1 0 0 1 1-1h3.5a1 1 0 0 1 1 1c0 1.25.2 2.45.6 3.6a1 1 0 0 1-.25 1z" fill="var(--accent-teal)"/></svg>
          <svg viewBox="0 0 24 24" aria-label="email"><rect x="2.5" y="5" width="19" height="14" rx="1.5" fill="none" stroke="var(--accent-teal)" stroke-width="2"/><path d="M3 6l9 7 9-7" fill="none" stroke="var(--accent-teal)" stroke-width="2"/></svg>
          <svg viewBox="0 0 24 24" aria-label="website"><circle cx="12" cy="12" r="9.5" fill="none" stroke="var(--accent-teal)" stroke-width="2"/><ellipse cx="12" cy="12" rx="4" ry="9.5" fill="none" stroke="var(--accent-teal)" stroke-width="1.6"/><path d="M2.5 12h19M4 7h16M4 17h16" stroke="var(--accent-teal)" stroke-width="1.6"/></svg>
        </span>
      </div>
      <div class="contact-lines">
        <div class="contact-phone">0491 362 517</div>
        <div class="contact-email">bec@clearpathcoaching.example.au</div>
        <div class="contact-web">www.clearpathcoaching.example.au</div>
      </div>
    </div>
  </section>
</main>
</body>
</html>
```